Carwash Signage

We own and operate a 25m tunnel car wash in the uk. We are looking to upgrade our signage to include the following:-

Wash selection Board Size-1300x1300mm
Conditions 1300x1300mm
Instructions 1300x1300mm
Banner 2600x600mm
Stamp card flyer a5 double sided - 9 squares for stamping 3rd square needs to say free air freshener 9th square needs to say free vip car wash.

I have attached some notes for the details that are required to be included.

We are looking for a modern smart look more European car wash style than American car wash style. It should be bold and clear. with yellow/orange & blue/green,grey colours

The final design must be in a industry standard printable format.

UPDATED BRIEF AS DISCUSSED: We require design for 2 x window decals, flag design and 50% off voucher. Attached are rough layout drawings of what they should look like - we expect the designs to be in keeping with the previous designs colours, etc that have been carried out. We Look forward to hearing from you.

Target Market(s)

local car owners within a 15-20 mile radius

Colors
0054AA
0677BA
7BADD7
CADEEF
E8F1F8
0094D4
00A9DD
6FCCEA
C7EBF8
E9F6FB
00AB8E
00BBA5
67D7C9
C6EFE9
E9F9F6

Requirements
Must have
• must be sharp and modern European look

```html
<!DOCTYPE html>
<html lang="en">
<head>
<meta charset="UTF-8">
<title>Meridian Car Wash – Loyalty Stamp Card</title>
<link href="https://fonts.googleapis.com/css2?family=Montserrat:wght@300;400;600;700;800&display=swap" rel="stylesheet">
<style>
  :root {
    --backdrop: #8a8a8a;
    --white: #ffffff;
    --brand-navy: #2b3aa6;
    --accent-orange: #f5b223;
    --accent-yellow: #f3de2a;
    --photo-top: #2a7898;
    --photo-mid: #1f5670;
    --photo-bottom: #27394a;
    --band-dark: #2a3b4b;
    --card-top: #1f6c93;
    --card-bottom: #1e3a52;
    --box-fill: #f2f2f2;
    --box-border: #f0d03c;
    --box-text: #4a4a4a;
  }
  * { box-sizing: border-box; margin: 0; padding: 0; }
  html, body { width: 1200px; height: 1000px; overflow: hidden; }
  body {
    background: var(--backdrop);
    font-family: "Montserrat", Arial, sans-serif;
    position: relative;
  }
  .card {
    position: absolute;
    top: 145px;
    width: 501px;
    height: 710px;
    overflow: hidden;
  }
  .card--front { left: 84px; }
  .card--back {
    left: 616px;
    background: linear-gradient(180deg, var(--card-top) 0%, var(--card-bottom) 100%);
  }

  /* Front */
  .brand-header {
    position: absolute; left: 0; top: 0; width: 100%; height: 173px;
    background: var(--white);
    color: var(--brand-navy);
    font-weight: 700;
    text-align: right;
    padding: 30px 36px 0 0;
  }
  .brand-header__service { font-size: 24px; letter-spacing: 2px; line-height: 1; }
  .brand-header__name { font-size: 58px; letter-spacing: 1px; line-height: 1.15; }
  .hero-photo {
    position: absolute; left: 0; top: 173px; width: 100%; height: 537px;
    background: linear-gradient(180deg, var(--photo-top) 0%, var(--photo-mid) 45%, var(--photo-bottom) 100%);
  }
  .hero-copy {
    position: absolute; left: 0; top: 190px; width: 100%;
    text-align: center;
  }
  .hero-copy__tagline { color: var(--accent-orange); font-weight: 700; font-size: 20px; }
  .hero-copy__headline {
    color: var(--white); font-weight: 700; font-size: 39px; line-height: 52px; margin-top: 6px;
  }
  .hero-copy__rewards { color: var(--accent-yellow); font-weight: 700; font-size: 19px; margin-top: 8px; }
  .offer-band {
    position: absolute; left: 0; bottom: 0; width: 100%; height: 107px;
    background: var(--band-dark);
    color: var(--white);
    font-weight: 600; font-size: 20px; line-height: 26px;
    text-align: center;
    padding-top: 3px;
  }

  /* Back */
  .rewards-title {
    position: absolute; left: 0; top: 40px; width: 100%;
    text-align: center;
    color: var(--accent-orange);
    font-weight: 800; font-size: 42px; line-height: 52px; letter-spacing: 1px;
  }
  .stamp-grid {
    position: absolute; left: 34px; top: 163px;
    display: grid;
    grid-template-columns: repeat(3, 125px);
    grid-template-rows: 120px 120px 120px;
    column-gap: 29px;
    row-gap: 13px;
  }
  .stamp-grid > :nth-child(n+7) { margin-top: 12px; }
  .stamp-box {
    background: var(--box-fill);
    border: 2px solid var(--box-border);
    border-radius: 14px;
    display: flex; flex-direction: column; align-items: center; justify-content: center;
    color: var(--box-text);
    font-weight: 300;
    text-align: center;
    line-height: 1.2;
  }
  .stamp-box__big { font-size: 22px; }
  .stamp-box__small { font-size: 18px; }
  .stamp-box--vip .stamp-box__small { font-size: 21px; }
  .card-terms {
    position: absolute; left: 0; top: 585px; width: 100%;
    text-align: center;
    color: var(--accent-yellow);
    font-weight: 700; font-size: 15px; line-height: 20px;
  }
  .card-contact {
    position: absolute; left: 34px; right: 32px; top: 665px;
    display: flex; justify-content: space-between;
    color: var(--accent-orange);
    font-weight: 700; font-size: 16px;
  }
</style>
</head>
<body>

  <section class="card card--front">
    <header class="brand-header">
      <div class="brand-header__service">CAR WASH</div>
      <div class="brand-header__name">MERIDIAN</div>
    </header>
    <div class="hero-photo" role="img" aria-label="Photo of a car inside a tunnel car wash with blue lighting and rotating brushes"></div>
    <div class="hero-copy">
      <p class="hero-copy__tagline">YOUR CAR DESERVE THE BEST SHINE</p>
      <h1 class="hero-copy__headline">COLLECT STAMPS<br>&amp; GET REWARDS!</h1>
      <p class="hero-copy__rewards">CAR WASH Air Freshener VIP Wash</p>
    </div>
    <div class="offer-band">
      Get your card stamped each time you<br>
      wash. 3rd wash = Free Air Freshener<br>
      9th wash = FREE VIP Car Wash!
    </div>
  </section>

  <section class="card card--back">
    <h2 class="rewards-title">YOUR LOYALLITY<br>REWARDS</h2>
    <div class="stamp-grid">
      <div class="stamp-box"></div>
      <div class="stamp-box"></div>
      <div class="stamp-box">
        <span class="stamp-box__big">free air</span>
        <span class="stamp-box__small">freshener</span>
      </div>
      <div class="stamp-box"></div>
      <div class="stamp-box"></div>
      <div class="stamp-box"></div>
      <div class="stamp-box"></div>
      <div class="stamp-box"></div>
      <div class="stamp-box stamp-box--vip">
        <span class="stamp-box__big">free vip</span>
        <span class="stamp-box__small">car wash</span>
      </div>
    </div>
    <p class="card-terms">
      Present this card at each visit to collect your<br>
      stamp. Only valid at Meridian Car Wash,<br>
      One card per customer
    </p>
    <div class="card-contact">
      <span class="card-contact__phone">123-456-7890</span>
      <span class="card-contact__web">www.example.com</span>
    </div>
  </section>

</body>
</html>
```